Corvane Capital Business Cards

These are professional business cards that are for my family office.
Put fake emails and phone numbers as of now until I finalize those components. This family office controls my families investments, assets, and future. The cards should be professional.
..
.
.
.
I just uploaded another variation of a logo I would like to see as a business card to I am inbeteen which logo to use

Target Market(s)

business

Industry/Entity Type

business

Contact Information for Business Card

Professional, wealth related, finance related.

Requirements
Must have
• Logo

```html
<!DOCTYPE html>
<html lang="en">
<head>
<meta charset="utf-8">
<title>Corvane Capital Business Cards</title>
<link href="https://fonts.googleapis.com/css2?family=EB+Garamond:wght@400;500&display=swap" rel="stylesheet">
<style>
  :root {
    --backdrop: #d9d9db;
    --card: #f7f7f6;
    --ink: #2f3038;
    --ink-soft: #4a4b52;
    --rule: #8a8b90;
    --mark: #2f3038;
  }
  * { margin: 0; padding: 0; box-sizing: border-box; }
  html, body {
    width: 1200px; height: 900px; overflow: hidden;
    background: var(--backdrop);
    font-family: "EB Garamond", Georgia, serif;
    color: var(--ink);
  }
  .sheet {
    width: 1200px; height: 900px;
    display: flex; flex-direction: column;
    align-items: center; justify-content: center; gap: 56px;
  }
  .card {
    position: relative;
    width: 620px; height: 354px;
    background: var(--card);
    box-shadow: 0 10px 30px rgba(0,0,0,0.12);
  }
  /* front */
  .brand {
    position: absolute; display: flex; align-items: center; gap: 12px;
  }
  .brand-dot {
    border: 2px solid var(--mark); border-radius: 50%;
    flex: none;
  }
  .brand-name {
    font-weight: 400; letter-spacing: 0.14em; text-transform: uppercase;
    color: var(--mark); white-space: nowrap;
  }
  .front .brand { right: 44px; top: 84px; }
  .front .brand-dot { width: 30px; height: 30px; }
  .front .brand-name { font-size: 17px; }
  .front .divider {
    position: absolute; left: 40px; right: 40px; top: 190px;
    height: 1px; background: var(--rule);
  }
  .holder { position: absolute; left: 40px; top: 118px; }
  .holder-name {
    font-size: 36px; font-weight: 400; letter-spacing: 0.04em;
    text-transform: uppercase; line-height: 1;
  }
  .holder-role { font-size: 17px; color: var(--ink-soft); margin-top: 4px; }
  .address {
    position: absolute; left: 40px; top: 208px;
    font-size: 15px; line-height: 1.45; color: var(--ink-soft);
  }
  .contacts {
    position: absolute; left: 370px; top: 208px;
    list-style: none; font-size: 15px; line-height: 2.05; color: var(--ink-soft);
  }
  /* back */
  .back { display: flex; align-items: center; justify-content: center; }
  .back .brand { position: static; gap: 18px; }
  .back .brand-dot { width: 58px; height: 58px; border-width: 3px; }
  .back .brand-name { font-size: 36px; font-weight: 500; }
</style>
</head>
<body>
<main class="sheet">
  <section class="card front" aria-label="Card front">
    <div class="brand">
      <span class="brand-dot"></span>
      <span class="brand-name">Corvane Capital</span>
    </div>
    <div class="holder">
      <h1 class="holder-name">Elias Marrow</h1>
      <p class="holder-role">Manager</p>
    </div>
    <div class="divider"></div>
    <address class="address" style="font-style:normal">
      418 Harbor Ridge Rd Fairview,<br>Oregon. 97024, USA
    </address>
    <ul class="contacts">
      <li>P:+1 555 014 229</li>
      <li>M:info@corvanecapital.com</li>
      <li>W:www.corvanecapital.com</li>
    </ul>
  </section>

  <section class="card back" aria-label="Card back">
    <div class="brand">
      <span class="brand-dot"></span>
      <span class="brand-name">Corvane Capital</span>
    </div>
  </section>
</main>
</body>
</html>
```